Business Card Design Project

The logo I included in my order was a previous image that we've used for shirts, signs, magnets, etc. We've decided to go back to that logo, with some updates.
We need to add "Inc." after "Dunmore Roofing,"
Also, I need the logo with a transparent background so that I can use it on other projects.

The business cards will be the first item I order with the new logo. The employee's info is:
Glenn Parry
Sales Manager
484-610-3357
gparry@dunmoreroofinginc.example

Also, I want a "Find us on Chatterly" icon on the card, along with our web address, www.dunmoreroofinginc.example.

Any questions, please email or call me:
lindadunmore@mailbox.example
484-729-1186

Reason: This is the first time I've tried Pixel Forum.

My timetable changed and I need to select a design by the end of the work day, 6 hours from now.Thanks so much for all of the super designs.

Target Market(s)

Homeowners

Industry/Entity Type

Business

Font styles to use
Serif

Requirements
Must have
• Transparent background
Similar to logo in photo I sent you

```html
<!DOCTYPE html>
<html lang="en">
<head>
<meta charset="utf-8">
<title>Dunmore Roofing Inc. – Business Card</title>
<link rel="stylesheet" href="https://fonts.googleapis.com/css2?family=Cinzel:wght@400&family=Roboto+Condensed:wght@300;700&display=swap">
<style>
  :root {
    --page-bg: #e9e7e3;
    --card-dark: #1f1f1f;
    --card-mid: #3a3a3a;
    --brand-tint: #a9bcbb;
    --name-white: #f2f2f2;
    --muted-grey: #8f8f8f;
    --contact-white: #e6e6e6;
    --band-grey: #8e9c9b;
    --band-light: #a3b0af;
  }
  * { box-sizing: border-box; margin: 0; padding: 0; }
  html, body { width: 1200px; height: 1000px; overflow: hidden; }
  body { background: var(--page-bg); position: relative; }

  .business-card {
    position: absolute;
    left: 350px; top: 57px;
    width: 500px; height: 877px;
    border-radius: 14px;
    overflow: hidden;
    background: radial-gradient(ellipse 70% 45% at 50% 40%, var(--card-mid), var(--card-dark) 100%);
    text-align: center;
  }

  .brand-name {
    position: absolute;
    left: 0; right: 0; top: 250px;
    font-family: "Cinzel", serif;
    font-weight: 400;
    font-size: 44px;
    line-height: 54px;
    color: var(--brand-tint);
  }

  .employee-name {
    position: absolute;
    left: 0; right: 0; top: 416px;
    font-family: "Cinzel", serif;
    font-weight: 400;
    font-size: 42px;
    line-height: 48px;
    color: var(--name-white);
    letter-spacing: 0.5px;
  }
  .employee-title {
    position: absolute;
    left: 0; right: 0; top: 461px;
    font-family: "Roboto Condensed", sans-serif;
    font-weight: 300;
    font-size: 20px;
    line-height: 24px;
    color: var(--muted-grey);
  }
  .employee-contact {
    position: absolute;
    left: 0; right: 0; top: 502px;
    font-family: "Roboto Condensed", sans-serif;
    font-weight: 300;
    font-size: 22px;
    line-height: 30px;
    color: var(--contact-white);
  }

  .company-band {
    position: absolute;
    left: 0; right: 0; top: 728px;
    height: 83px;
    background: linear-gradient(100deg, var(--band-grey), var(--band-light) 50%, var(--band-grey));
    color: var(--name-white);
    font-family: "Cinzel", serif;
  }
  .company-phone {
    display: block;
    padding-top: 4px;
    font-size: 34px;
    line-height: 40px;
  }
  .company-web {
    display: block;
    font-size: 25px;
    line-height: 30px;
  }
  .company-web small { font-size: 15px; text-transform: lowercase; }

  .social-link {
    position: absolute;
    left: 0; right: 0; top: 830px;
    display: flex; justify-content: center; align-items: center; gap: 6px;
    font-family: "Roboto Condensed", sans-serif;
    font-weight: 700;
    font-size: 15px;
    color: var(--name-white);
  }
  .social-link .social-square {
    width: 10px; height: 10px; background: var(--name-white);
  }
</style>
</head>
<body>
  <article class="business-card">
    <h1 class="brand-name">Dunmore<br>Roofing Inc.</h1>

    <h2 class="employee-name">Glenn Parry</h2>
    <p class="employee-title">sales manager</p>
    <p class="employee-contact">
      p: (484) 610-3357<br>
      e: gParry@DunmoreRoofingInc.example
    </p>

    <div class="company-band">
      <span class="company-phone">(610) 555-0148</span>
      <span class="company-web">DunmoreRoofingInc<small>.example</small></span>
    </div>

    <p class="social-link"><span class="social-square"></span>Find us on Chatterly</p>
  </article>
</body>
</html>
```